Business Card design for law firm = Brightvale Australia

We are seeking a new design for our business cards.
We are keeping our logo, which is attached.
We need space for
Name
Title
Address is , which is
Level 7
214 Marlowe Street
Sydney NSW 2047
Phone :
Mobile :
Fax :
Email :
DX :
website www.brightvale-example.com.au

Industry/Entity Type

Law Firm / Banking and Finance

Contact Information for Business Card

We are seeking a new design for our business cards. We are keeping our logo. We need space for Name Title Address is Level 7 214 Marlowe Street Sydney NSW 2047 Phone Mobile Fax Email DX website www.brightvale-example.com.au

Colors
0054AA
0677BA
7BADD7
CADEEF
E8F1F8

Requirements
Must have
• see our website for general feel www.brightvale-example.com.au

```html
<!DOCTYPE html>
<html lang="en">
<head>
<meta charset="utf-8">
<title>Brightvale Australia – Business Card</title>
<link href="https://fonts.googleapis.com/css2?family=Oswald:wght@600&family=Open+Sans:wght@400&family=Arimo:wght@400&display=swap" rel="stylesheet">
<style>
  :root {
    --backdrop: #1c1c1e;
    --card: #111112;
    --blue-deep: #0054AA;
    --blue-main: #0677BA;
    --blue-bright: #11A7E0;
    --text-light: #f2f2f2;
    --divider: #6a6a6a;
  }
  * { box-sizing: border-box; margin: 0; padding: 0; }
  html, body { width: 1200px; height: 900px; overflow: hidden; }
  body {
    background: var(--backdrop);
    display: flex;
    flex-direction: column;
    align-items: center;
    justify-content: center;
    gap: 44px;
  }
  .card {
    position: relative;
    width: 640px;
    height: 366px;
    background: var(--card);
    box-shadow: 0 10px 30px rgba(0,0,0,.5);
  }
  .card__band {
    position: absolute;
    left: 0; right: 0; bottom: 0;
    height: 9px;
    background: linear-gradient(90deg, var(--blue-main), var(--blue-bright));
  }

  /* Front */
  .front {
    display: flex;
    flex-direction: column;
    align-items: center;
    padding-top: 104px;
  }
  .brand__name {
    font-family: "Open Sans", sans-serif;
    font-weight: 400;
    font-size: 58px;
    line-height: 1;
    color: var(--blue-main);
  }
  .tagline {
    margin-top: 14px;
    font-family: "Open Sans", sans-serif;
    font-size: 19px;
    letter-spacing: 2.4px;
    color: var(--blue-main);
  }
  .dx {
    margin-top: 26px;
    font-family: "Arimo", sans-serif;
    font-size: 17px;
    color: var(--text-light);
  }
  .dx__label { color: var(--blue-main); }

  /* Back */
  .back__identity {
    position: absolute;
    left: 40px; top: 112px;
    width: 268px;
    text-align: right;
  }
  .person__name {
    font-family: "Oswald", sans-serif;
    font-weight: 600;
    font-size: 38px;
    line-height: 1;
    letter-spacing: -0.5px;
    color: var(--blue-main);
  }
  .person__title {
    margin-top: 4px;
    font-family: "Arimo", sans-serif;
    font-size: 18px;
    color: var(--blue-bright);
  }
  .back__divider {
    position: absolute;
    left: 330px; top: 110px;
    width: 1px; height: 116px;
    background: var(--divider);
  }
  .contact {
    position: absolute;
    left: 352px; top: 108px;
    list-style: none;
    font-family: "Arimo", sans-serif;
    font-size: 16px;
    color: var(--text-light);
  }
  .contact__item {
    display: flex;
    align-items: center;
    gap: 9px;
    height: 24px;
    white-space: nowrap;
  }
  .contact__icon { width: 16px; height: 16px; flex: none; fill: var(--blue-main); }
  .contact__accent { color: var(--blue-bright); }
  .address {
    position: absolute;
    left: 70px; bottom: 44px;
    display: flex;
    align-items: center;
    gap: 9px;
    font-family: "Arimo", sans-serif;
    font-size: 17px;
    color: var(--text-light);
  }
</style>
</head>
<body>

<section class="card front" aria-label="Business card front">
  <p class="brand__name">Brightvale</p>
  <p class="tagline">strategic legal outsourcing</p>
  <p class="dx"><span class="dx__label">DX :</span>100200300</p>
  <span class="card__band"></span>
</section>

<section class="card back" aria-label="Business card back">
  <div class="back__identity">
    <h1 class="person__name">DANIEL HARTLEY</h1>
    <p class="person__title">Managing Director</p>
  </div>
  <span class="back__divider"></span>
  <ul class="contact">
    <li class="contact__item">
      <svg class="contact__icon" viewBox="0 0 16 16"><path d="M3.5 1.5l2.5 0 1 3.5-1.8 1.3c.8 1.8 2.2 3.2 4 4l1.3-1.8 3.5 1v2.5c0 .8-.7 1.5-1.5 1.5C6.8 13.5 2 8.7 2 3c0-.8.7-1.5 1.5-1.5z"/></svg>
      <span>044-555 010 222</span>
    </li>
    <li class="contact__item">
      <svg class="contact__icon" viewBox="0 0 16 16"><path d="M4.5 1h7c.6 0 1 .4 1 1v12c0 .6-.4 1-1 1h-7c-.6 0-1-.4-1-1V2c0-.6.4-1 1-1zm.5 2v9h6V3H5zm3 9.8a.8.8 0 100 1.6.8.8 0 000-1.6z"/></svg>
      <span>044-555 010 333</span>
    </li>
    <li class="contact__item">
      <svg class="contact__icon" viewBox="0 0 16 16"><path d="M4 1h8v4H4zM2 6h12c.6 0 1 .4 1 1v5h-3v3H4v-3H1V7c0-.6.4-1 1-1zm3 5v3h6v-3H5z"/></svg>
      <span>044-555 010 444</span>
    </li>
    <li class="contact__item">
      <svg class="contact__icon" viewBox="0 0 16 16"><path d="M1 3h14v10H1V3zm1.5 1.2v.3L8 8.6l5.5-4.1v-.3h-11zm0 1.9v5.7h11V6.1L8 10.2 2.5 6.1z"/></svg>
      <span>info@brightvale-example.com</span>
    </li>
    <li class="contact__item">
      <svg class="contact__icon" viewBox="0 0 16 16"><path d="M8 1a7 7 0 100 14A7 7 0 008 1zm5.4 6.3h-2.6c-.1-1.9-.5-3.5-1.1-4.6a5.6 5.6 0 013.7 4.6zM8 2.4c.6.6 1.300 2.3 1.4 4.9H6.6C6.7 4.7 7.4 3 8 2.4zM6.3 2.7c-.6 1.1-1 2.7-1.1 4.6H2.6a5.6 5.6 0 013.7-4.6zM2.6 8.7h2.6c.1 1.9.5 3.5 1.1 4.6a5.6 5.6 0 01-3.7-4.6zM8 13.6c-.6-.6-1.3-2.3-1.4-4.9h2.8c-.1 2.6-.8 4.3-1.4 4.9zm1.7-.3c.6-1.1 1-2.7 1.1-4.6h2.6a5.6 5.6 0 01-3.7 4.6z"/></svg>
      <span>www.<span class="contact__accent">brightvale-example</span>.com.au</span>
    </li>
  </ul>
  <p class="address">
    <svg class="contact__icon" viewBox="0 0 16 16"><path d="M8 0.5a5 5 0 00-5 5c0 3.8 5 10 5 10s5-6.2 5-10a5 5 0 00-5-5zm0 7a2 2 0 110-4 2 2 0 010 4z"/></svg>
    <span>Level 7, 214 Marlowe Street, Sydney NSW 2047</span>
  </p>
  <span class="card__band"></span>
</section>

</body>
</html>
```